Local Flower Farm Needs Business Card Design

I need business cards designed for a flower farm based in Eudora, Kansas.
Business Info:
We are a local cut flower farm located in Eudora, Kansas, founded by Corinne Haldwick. What started as a passion for agriculture and search for more joy in daily life has blossomed into a small business dedicated to providing the community with beautiful, fresh, and sustainable flowers. We specialize in local, seasonal blooms, ensuring that every petal reflects the care and dedication we pour into our craft. Our mission is to deliver the highest quality flowers directly to our customers through local farmers markets and to florists who share our commitment to sustainability. Join us in celebrating the beauty of nature, one bloom at a time!
Contact Details:
Corinne Haldwick
Owner
Phone 913-555-0147
Facebook: Rosalind Thorpe Gardens
Instagram: @RosalindThorpeGardens
Website: RosalindThorpeGardens.example
Target Market(s)
Wholesale to Florists and Direct to Consumer via Farmers Market
Industry/Entity Type
Florist, Farm
Contact Information for Business Card
Name, Contact Info, Logo
Look and feel
Each slider illustrates characteristics of the customer's brand and the style your logo design should communicate.

```html
<!DOCTYPE html>
<html lang="en">
<head>
<meta charset="utf-8">
<title>Rosalind Thorpe Gardens — Business Card</title>
<link rel="stylesheet" href="https://fonts.googleapis.com/css2?family=Tinos:wght@400;700&display=swap">
<style>
  :root {
    --ink: #0b2830;
    --text: #111111;
    --paper: #ffffff;
    --backdrop: #e3e7e9;
    --rule: #6b6f71;
  }
  * { margin: 0; padding: 0; box-sizing: border-box; }
  html, body { width: 1200px; height: 960px; overflow: hidden; }
  body {
    background: var(--backdrop);
    font-family: "Tinos", "Times New Roman", serif;
    color: var(--text);
    position: relative;
  }
  .card {
    position: absolute;
    left: 249px;
    width: 702px;
    height: 400px;
    background: var(--paper);
    border-radius: 30px;
    overflow: hidden;
  }
  .card--front { top: 60px; }
  .card--back { top: 500px; }
  .edge-band {
    position: absolute;
    top: 100px;
    width: 16px;
    height: 200px;
    background: var(--ink);
  }
  .edge-band--left { left: 0; }
  .edge-band--right { right: 0; }

  .brand-seal {
    position: absolute;
    border: 1.5px solid var(--ink);
    border-radius: 50%;
    display: flex;
    align-items: center;
    justify-content: center;
    text-align: center;
    color: var(--ink);
    font-weight: 400;
    text-transform: uppercase;
    letter-spacing: 0.12em;
  }
  .card--front .brand-seal {
    left: 226px; top: 76px; width: 248px; height: 248px;
    font-size: 24px; line-height: 1.35;
  }
  .card--back .brand-seal {
    left: 57px; top: 89px; width: 228px; height: 228px;
    font-size: 22px; line-height: 1.35;
  }

  .divider {
    position: absolute;
    left: 350px; top: 80px;
    width: 1px; height: 241px;
    background: var(--rule);
  }
  .contact-block {
    position: absolute;
    left: 390px; top: 102px;
  }
  .person-name {
    font-size: 33px;
    font-weight: 700;
    letter-spacing: 0.02em;
    line-height: 1.1;
  }
  .person-role {
    font-size: 17px;
    letter-spacing: 0.04em;
    line-height: 1.1;
  }
  .contact-list {
    list-style: none;
    margin-top: 54px;
  }
  .contact-list li {
    display: flex;
    align-items: center;
    gap: 8px;
    font-size: 18px;
    letter-spacing: 0.03em;
    height: 23.5px;
  }
  .contact-list svg { width: 17px; height: 17px; flex: none; }
</style>
</head>
<body>
  <section class="card card--front" aria-label="Card front">
    <div class="edge-band edge-band--left"></div>
    <div class="edge-band edge-band--right"></div>
    <div class="brand-seal">Rosalind<br>Thorpe<br>Gardens</div>
  </section>

  <section class="card card--back" aria-label="Card back">
    <div class="edge-band edge-band--left"></div>
    <div class="edge-band edge-band--right"></div>
    <div class="brand-seal">Rosalind<br>Thorpe<br>Gardens</div>
    <div class="divider"></div>
    <div class="contact-block">
      <h1 class="person-name">Corinne Haldwick</h1>
      <p class="person-role">Owner</p>
      <ul class="contact-list">
        <li>
          <svg viewBox="0 0 24 24" aria-hidden="true"><path fill="#111" d="M6.6 10.8a15.1 15.1 0 0 0 6.6 6.6l2.2-2.2c.3-.3.7-.4 1-.2 1.1.4 2.3.6 3.6.6.6 0 1 .4 1 1V20c0 .6-.4 1-1 1A17 17 0 0 1 3 4c0-.6.4-1 1-1h3.5c.6 0 1 .4 1 1 0 1.3.2 2.5.6 3.6.1.3 0 .7-.2 1z"/></svg>
          913-555-0147
        </li>
        <li>
          <svg viewBox="0 0 24 24" aria-hidden="true"><circle cx="12" cy="12" r="11" fill="#111"/></svg>
          Rosalind Thorpe Gardens
        </li>
        <li>
          <svg viewBox="0 0 24 24" aria-hidden="true"><rect x="2" y="2" width="20" height="20" rx="5" fill="none" stroke="#111" stroke-width="2.4"/></svg>
          @RosalindThorpeGardens
        </li>
        <li>
          <svg viewBox="0 0 24 24" aria-hidden="true"><circle cx="12" cy="12" r="10" fill="none" stroke="#111" stroke-width="2"/><ellipse cx="12" cy="12" rx="4" ry="10" fill="none" stroke="#111" stroke-width="1.6"/><line x1="2" y1="12" x2="22" y2="12" stroke="#111" stroke-width="1.6"/></svg>
          RosalindThorpeGardens.example
        </li>
      </ul>
    </div>
  </section>
</body>
</html>
```